Brand new letterhead, business card, email signature etc.

We are a financial company in London, UK. Our website is www.marlowvane.com. We're wanting a complete remodel of the company colours, letter head, business cards, email signatures, etc. Looking to keep the same font for the company name. I have upload a colour palette that we want to work with. We're looking for company letterhead for outgoing letters/ correspondence, letterhead for internal documentation, email signatures, e-letters. etc. Ultimately we will redesign the entire website also. It is important that our clients get a strong, secure, warm, trustworthy, solid feeling and first impression.
Updates

Designs look the same

Target Market(s)

Institutional investors, (ultra) high net worth individuals

Industry/Entity Type

Finance, Invesments banking.

Font styles to use
Other font styles liked:
• Current font is "Champagne & Limousines"

Requirements
Must have
• Must use the colours provided on the PDF uploaded to the portal. The purple = main colour. The red = accent colour.
Nice to have
• Nice to use same font as now for the company name "Corvane". Font is "Champagne & Limousines". Nice to have some reference to the old logo flower, but only subtle.
Should not have
• Do not use the colour red from our website. Use the colours provided on the colour palette PDF that I uploaded in the portal.

```html
<!DOCTYPE html>
<html lang="en">
<head>
<meta charset="utf-8">
<title>Corvane — Business Card</title>
<link rel="stylesheet" href="https://fonts.googleapis.com/css2?family=Josefin+Sans:wght@300;400;600&display=swap">
<style>
  :root {
    --page-bg: #e9e9e9;
    --card-white: #f4f4f3;
    --card-cream: #e2ddd0;
    --accent-red: #d20000;
    --deep-plum: #2a0a18;
    --text-grey: #3f3f3f;
    --rule-grey: #cfcfc4;
    --frame-white: #ffffff;
  }
  * { margin: 0; padding: 0; box-sizing: border-box; }
  html, body {
    width: 1200px; height: 900px; overflow: hidden;
    background: var(--page-bg);
    font-family: "Josefin Sans", sans-serif;
  }
  .canvas { position: relative; width: 1200px; height: 900px; }

  .card {
    position: absolute; left: 270px;
    width: 660px; height: 377px;
    box-shadow: 0 6px 18px rgba(0,0,0,0.14);
    overflow: hidden;
  }

  /* Back side */
  .card--back { top: 50px; background: var(--card-cream); }
  .back-mark {
    position: absolute; left: 50%; top: 88px; transform: translateX(-50%);
    display: flex; align-items: center; gap: 22px;
  }
  .back-mark__square {
    width: 130px; height: 130px;
    background: var(--frame-white);
    border: 2px solid var(--deep-plum);
    outline: 8px solid var(--frame-white);
  }
  .back-mark__name {
    font-weight: 300; font-size: 44px; letter-spacing: 8px;
    color: var(--deep-plum);
  }
  .back-url {
    position: absolute; left: 0; right: 0; bottom: 70px;
    text-align: center;
    font-weight: 400; font-size: 15px; letter-spacing: 5px;
    color: var(--text-grey);
  }

  /* Front side */
  .card--front { top: 473px; background: var(--card-white); }
  .front-band {
    position: absolute; left: 0; top: 0; width: 100%; height: 26px;
    background: var(--accent-red);
  }
  .contact-column {
    position: absolute; left: 582px; top: 0; width: 43px; height: 208px;
    background: var(--deep-plum);
  }
  .contact-icon { position: absolute; left: 10px; width: 23px; height: 23px; }
  .contact-icon--phone { top: 68px; }
  .contact-icon--web { top: 120px; }
  .contact-icon--pin { top: 171px; }

  .brand {
    position: absolute; left: 35px; top: 61px;
    display: flex; align-items: center; gap: 14px;
  }
  .brand__square {
    width: 59px; height: 59px;
    border: 1px solid var(--deep-plum);
  }
  .brand__name {
    font-weight: 300; font-size: 33px; letter-spacing: 6px;
    color: var(--deep-plum); padding-top: 6px;
  }

  .contact-group {
    position: absolute; right: 89px;
    text-align: right; font-weight: 300; font-size: 15px; line-height: 19px;
    color: var(--text-grey);
  }
  .contact-group--phone { top: 58px; }
  .contact-group--web { top: 112px; }
  .contact-group--address { top: 165px; }

  .contact-rule {
    position: absolute; left: 382px; width: 200px; height: 1px;
    background: var(--rule-grey);
  }
  .contact-rule--first { top: 106px; }
  .contact-rule--second { top: 154px; }

  .holder {
    position: absolute; left: 35px; top: 293px;
    color: var(--deep-plum);
  }
  .holder__name { font-weight: 600; font-size: 21px; line-height: 22px; }
  .holder__role { font-weight: 400; font-size: 13px; line-height: 16px; }
</style>
</head>
<body>
<main class="canvas">

  <section class="card card--back" aria-label="Card back">
    <div class="back-mark">
      <div class="back-mark__square"></div>
      <span class="back-mark__name">CORVANE</span>
    </div>
    <p class="back-url">www.marlowvane.com</p>
  </section>

  <section class="card card--front" aria-label="Card front">
    <div class="front-band"></div>

    <div class="brand">
      <div class="brand__square"></div>
      <span class="brand__name">CORVANE</span>
    </div>

    <div class="contact-group contact-group--phone">
      <p>+000 12345 6789</p>
      <p>+000 12345 6789</p>
    </div>
    <div class="contact-rule contact-rule--first"></div>
    <div class="contact-group contact-group--web">
      <p>urwebsitename.com</p>
      <p>urname@email.com</p>
    </div>
    <div class="contact-rule contact-rule--second"></div>
    <div class="contact-group contact-group--address">
      <p>1234 Street name, town/city,</p>
      <p>state/country, post/zip 012345.</p>
    </div>

    <div class="contact-column">
      <svg class="contact-icon contact-icon--phone" viewBox="0 0 24 24" aria-label="Phone">
        <path d="M3 9c0-3 4-4 9-4s9 1 9 4v1h-4V8.5c-1.5-.6-3-.8-5-.8s-3.5.2-5 .8V10H3z" fill="#fff"/>
        <path d="M7 11h10l2 8H5z" fill="#fff"/>
        <circle cx="12" cy="15" r="2" fill="#2a0a18"/>
      </svg>
      <svg class="contact-icon contact-icon--web" viewBox="0 0 24 24" fill="none" stroke="#fff" stroke-width="1.6" aria-label="Web">
        <circle cx="12" cy="12" r="9"/>
        <path d="M3 12h18M12 3c3 3 3 15 0 18M12 3c-3 3-3 15 0 18"/>
      </svg>
      <svg class="contact-icon contact-icon--pin" viewBox="0 0 24 24" aria-label="Location">
        <path d="M12 2a7 7 0 0 0-7 7c0 5 7 13 7 13s7-8 7-13a7 7 0 0 0-7-7z" fill="#fff"/>
        <circle cx="12" cy="9" r="2.5" fill="#2a0a18"/>
      </svg>
    </div>

    <div class="holder">
      <p class="holder__name">Elliot Marsh</p>
      <p class="holder__role">Designation</p>
    </div>
  </section>

</main>
</body>
</html>
```